Mental Health care Company in Washington DC

We are a new mental health care services provider in Washington DC. Please look at these sites.
https://brightwaterfamilysupport.com
https://www.quietharborinc.com
https://willowgate-dc.org/
https://www.tidepathdc.com
https://www.thelanternofdc.com

```html
<!DOCTYPE html>
<html lang="en">
<head>
<meta charset="utf-8">
<title>Lumen Health Services</title>
<link href="https://fonts.googleapis.com/css2?family=Montserrat:wght@400;500;600;700;800&family=Poppins:wght@400;500;600&display=swap" rel="stylesheet">
<style>
:root{
  --navy:#0f1f3d;
  --orange:#f58a2e;
  --teal:#a9dde0;
  --teal-dark:#7fc7cc;
  --grey-band:#efefef;
  --text:#3d4450;
  --muted:#9aa0a8;
  --white:#ffffff;
  --line:#d9dde2;
}
*{box-sizing:border-box;margin:0;padding:0}
html,body{width:1200px;height:4364px;overflow:hidden}
body{position:relative;font-family:"Poppins",sans-serif;color:var(--text);background:var(--white)}
.abs{position:absolute}
h1,h2,h3{font-weight:400}
.heading{font-family:"Montserrat",sans-serif;font-weight:400;color:var(--navy);text-transform:uppercase;letter-spacing:.5px}
.heading b{font-weight:800}
.body-copy{font-size:13px;line-height:21.5px;color:var(--text)}

/* header */
.topbar{left:470px;top:0;width:730px;height:32px;background:var(--navy);clip-path:polygon(18px 0,100% 0,100% 100%,40px 100%)}
.topbar-accent{left:470px;top:0;width:30px;height:32px;background:var(--orange);clip-path:polygon(0 0,18px 0,40px 100%,22px 100%)}
.topbar-item{top:9px;font-size:10px;color:#c8ced8;display:flex;align-items:center;gap:5px;white-space:nowrap}
.topbar-item b{color:#fff;font-weight:500}
.brand{left:92px;top:22px;display:flex;align-items:center;gap:8px}
.brand-dot{width:12px;height:12px;border-radius:50%;background:var(--orange)}
.brand-name{font-family:"Montserrat",sans-serif;font-size:30px;font-weight:500;color:var(--navy);letter-spacing:-.5px}
.brand-sub{left:122px;top:60px;font-size:10px;letter-spacing:5px;color:var(--muted)}
.nav a{position:absolute;top:55px;font-size:12px;color:var(--navy);text-decoration:none}
.nav a.active{color:var(--orange);font-weight:500}
.btn{position:absolute;display:flex;align-items:center;justify-content:center;font-family:"Montserrat",sans-serif;font-weight:600;font-size:11px;text-transform:uppercase}
.btn-contact{left:995px;top:47px;width:108px;height:30px;border-radius:15px;background:var(--orange);color:#fff;text-transform:none;font-size:10px}

/* hero */
.hero-photo{left:0;top:90px;width:1200px;height:532px;background:linear-gradient(110deg,#b78a6c 0%,#cfc7bf 35%,#d9d9d6 60%,#a7b2bd 100%)}
.hero-card{left:131px;top:208px;width:496px;height:296px;background:#fff;border-radius:6px;box-shadow:0 6px 24px rgba(0,0,0,.12);text-align:center}
.hero-title{margin-top:34px;font-family:"Montserrat",sans-serif;font-size:30px;line-height:44px;color:var(--navy);font-weight:400}
.hero-title span{color:var(--orange);font-weight:700}
.hero-text{margin:12px auto 0;width:420px;font-size:13px;line-height:21px;color:var(--navy)}
.hero-form{left:34px;top:204px;width:428px;height:60px;display:flex;position:absolute}
.hero-input{flex:1;background:#e8e8e8;border-radius:8px 0 0 8px;font-size:11px;font-weight:500;color:var(--navy);display:flex;align-items:center;padding-left:22px}
.hero-submit{width:101px;background:var(--navy);color:#fff;border-radius:0 8px 8px 0;font-size:10px;font-weight:600;display:flex;align-items:center;justify-content:center}

/* about */
.about-glow{left:0;top:660px;width:640px;height:600px;background:radial-gradient(ellipse at 45% 45%,#e6edf0 0%,#ffffff 70%)}
.about-photo{left:140px;top:730px;width:460px;height:460px;border-radius:10px;background:linear-gradient(135deg,#a9cdd3 0%,#b3a796 50%,#8d9a93 100%);opacity:.85}
.about-title{left:668px;top:758px;font-size:30px}
.about-sub{left:666px;top:798px;font-family:"Montserrat",sans-serif;font-size:21px;color:var(--muted);display:flex;align-items:center;gap:8px}
.about-sub i{display:block;width:82px;height:1px;background:var(--muted)}
.about-copy{left:667px;top:840px;width:392px}
.about-copy p+p{margin-top:12px}
.btn-readmore{left:668px;top:1116px;width:126px;height:40px;background:var(--teal);color:var(--navy)}

/* services */
.band{left:0;width:1200px;background:var(--grey-band)}
.section-title{left:0;width:1200px;text-align:center;font-size:31px}
.service-card{top:1436px;width:284px;height:306px;background:#fff;border-radius:8px;box-shadow:0 4px 16px rgba(0,0,0,.05);text-align:center}
.service-icon{margin:34px auto 0;width:84px;height:84px;border-radius:50%;border:1.5px dashed var(--teal-dark);display:flex;align-items:center;justify-content:center}
.service-icon i{width:70px;height:70px;border-radius:50%;display:flex;align-items:center;justify-content:center}
.service-name{margin-top:20px;font-family:"Montserrat",sans-serif;font-size:17px;font-weight:600;color:var(--navy)}
.service-text{margin:10px auto 0;width:244px}

/* testimonials */
.avatar{border-radius:50%;background:radial-gradient(circle at 50% 40%,#d8d2cc,#8f8a86)}
.stars{left:0;top:1996px;width:1200px;text-align:center;color:var(--orange);font-size:20px;letter-spacing:4px}
.quote{left:320px;top:2035px;width:560px;text-align:center;font-style:italic;font-size:14px;line-height:24px;color:var(--navy)}
.client-name{left:0;top:2174px;width:1200px;text-align:center;font-family:"Montserrat",sans-serif;font-weight:700;font-size:16px;color:var(--navy);letter-spacing:.5px}
.client-place{left:0;top:2201px;width:1200px;text-align:center;font-size:14px;color:var(--navy)}
.dots{left:575px;top:2233px;display:flex;gap:10px}
.dots i{width:9px;height:9px;border-radius:50%;border:1px solid var(--muted)}
.dots i.on{background:var(--teal-dark);border-color:var(--teal-dark)}

/* why choose */
.feature-title{font-family:"Montserrat",sans-serif;font-weight:600;font-size:18px;color:var(--navy)}
.feature-text{font-size:13px;line-height:21.5px;margin-top:8px}
.feature-left{left:100px;top:2550px;width:262px;text-align:right}
.feature-right{left:832px;top:2550px;width:262px}
.feature-bottom{left:668px;top:2887px;width:250px}

/* contact */
.contact-intro{left:0;top:3206px;width:1200px;text-align:center}
.field{height:40px;border:1px solid var(--line);border-radius:3px;display:flex;align-items:center;font-size:11px;color:var(--navy);background:#fff}
.field-icon{width:36px;height:100%;display:flex;align-items:center;justify-content:center;border-right:1px solid var(--line);margin-right:11px}
.field-area{height:84px;align-items:flex-start}
.field-area .field-icon{height:28px;border-right:none;margin-top:8px}
.field-area span{margin-top:13px}
.btn-submit{left:536px;top:3494px;width:127px;height:40px;background:var(--teal);color:var(--navy)}

/* cta */
.cta-photo{left:0;top:3627px;width:1200px;height:351px;background:linear-gradient(180deg,#6f8596 0%,#8ea3b0 35%,#3e5a54 60%,#5d7f93 78%,#2f4b63 100%)}
.cta-title{left:0;top:3693px;width:1200px;text-align:center;font-family:"Montserrat",sans-serif;font-size:26px;font-weight:400;color:#fff;letter-spacing:.5px}
.cta-title b{font-weight:800}
.cta-sub{left:0;top:3740px;width:1200px;text-align:center;font-size:21px;color:#fff}
.btn-cta{left:497px;top:3800px;width:205px;height:40px;background:var(--orange);color:var(--navy);font-size:12px;border-radius:3px}

/* footer */
.footer{left:0;top:3978px;width:1200px;height:386px;background:var(--navy)}
.footer-head{font-family:"Montserrat",sans-serif;font-weight:700;font-size:15px;color:#fff}
.footer-head i{display:block;width:24px;height:2px;background:#fff;margin-top:8px}
.footer-list{list-style:none;margin-top:18px;font-size:12px;color:#fff;line-height:28px}
.contact-row{display:flex;gap:9px;margin-top:14px;color:#fff;font-size:12px;line-height:18px}
.contact-row b{font-weight:600;display:block}
.social-row{display:flex;align-items:center;gap:10px;margin-top:12px;color:#fff;font-size:13px}
.social-row i{width:28px;height:28px;border:1.5px solid #fff;border-radius:50%}
.footer-rule{left:143px;top:4310px;width:914px;height:1px;background:rgba(255,255,255,.2)}
.copyright{left:0;top:4330px;width:1200px;text-align:center;font-size:12px;color:#fff}
</style>
</head>
<body>

<!-- Header -->
<div class="abs topbar-accent"></div>
<div class="abs topbar"></div>
<div class="abs topbar-item" style="left:550px"><svg width="12" height="12" viewBox="0 0 24 24"><path fill="#f58a2e" d="M6.6 10.8a15 15 0 0 0 6.6 6.6l2.2-2.2c.3-.3.7-.4 1-.2 1.1.4 2.3.6 3.6.6.6 0 1 .4 1 1V20c0 .6-.4 1-1 1A17 17 0 0 1 3 4c0-.6.4-1 1-1h3.5c.6 0 1 .4 1 1 0 1.3.2 2.5.6 3.6.1.3 0 .7-.2 1z"/></svg>Call now: <b>(202) 555-0148</b></div>
<div class="abs topbar-item" style="left:715px"><svg width="13" height="10" viewBox="0 0 26 20"><rect width="26" height="20" rx="2" fill="#f58a2e"/><path d="M1 2l12 9 12-9" stroke="#0f1f3d" stroke-width="2" fill="none"/></svg>Email: <b>hello@lumenhealthdc.com</b></div>
<div class="abs topbar-item" style="left:900px"><svg width="12" height="12" viewBox="0 0 24 24"><circle cx="12" cy="12" r="11" fill="#f58a2e"/><path d="M12 6v6l4 2" stroke="#0f1f3d" stroke-width="2" fill="none"/></svg>Time: <b>Mon - Sun, 08:30am to 05:30pm</b></div>

<div class="abs brand"><span class="brand-dot"></span><span class="brand-name">Lumen Health</span></div>
<div class="abs brand-sub">SERVICES</div>
<nav class="nav">
  <a class="active" style="left:553px">Home</a>
  <a style="left:628px">About Us</a>
  <a style="left:723px">Services ⌄</a>
  <a style="left:825px">Blog</a>
  <a style="left:891px">FAQs</a>
</nav>
<div class="btn btn-contact">Contact Now</div>

<!-- Hero -->
<div class="abs hero-photo" role="img" aria-label="Photo of a clinician and nurse walking through a bright hospital ward"></div>
<div class="abs hero-card">
  <h1 class="hero-title">MENTAL WELLNESS<br>FOR A <span>STRONGER YOU</span></h1>
  <p class="hero-text">Evidence-based care tailored to your needs. Where clinical expertise meets your unique needs</p>
  <div class="hero-form">
    <div class="hero-input">Enter your email</div>
    <div class="hero-submit">Subscribe</div>
  </div>
</div>

<!-- About -->
<div class="abs about-glow"></div>
<div class="abs about-photo" role="img" aria-label="Photo of a woman holding a standing yoga balance pose"></div>
<h2 class="abs heading about-title">ABOUT <b>LUMEN HEALTH</b></h2>
<div class="abs about-sub">SERVICES<i></i></div>
<div class="abs body-copy about-copy">
  <p>Lorem ipsum dolor sit amet, consectetuer adipiscing elit sed diam nonummy nibh euismod tincidunt ut laoet dolo magna aliquam erat volutpat.</p>
  <p>Ut wisi enim ad minim veniam, quis nostrud exer ullamcorper suscipit lobortis nisl ut aliquip ex ea commodo consequat. Duis autem vel eum iriure dolor in hendrerit in vulputate velit esse molestie consequat, vel illum dolore eu feugilla facilisis at vero eros et accumsan et iusto odio dignissim qui blandit praesent luptatum zzril delenit augue duis dolore te feugait nulla facilisi. Lorem ipsum dolor sit amet, consectetuer adipiscing elit, sed diam nonummy.</p>
</div>
<div class="btn btn-readmore">Read More</div>

<!-- Services -->
<div class="abs band" style="top:1285px;height:551px"></div>
<h2 class="abs heading section-title" style="top:1368px">OUR <b>SERVICES</b></h2>
<div class="abs service-card" style="left:141px">
  <div class="service-icon"><i style="background:var(--teal)"><svg width="40" height="40" viewBox="0 0 40 40" fill="none" stroke="#0f1f3d" stroke-width="1.6"><circle cx="20" cy="10" r="4"/><path d="M8 30h24M10 30l4-10h12l4 10M14 24h12"/></svg></i></div>
  <h3 class="service-name">Individual Therapy</h3>
  <p class="body-copy service-text">Ut wisi enim ad minim v quis nostrud exerci taton ullamcorper spit lobortis nisl ut aliquip ex ea comghmodo consequat. Duis autem vel eum iriure dolor in hendrerit in vulputa.</p>
</div>
<div class="abs service-card" style="left:456px">
  <div class="service-icon" style="border-color:var(--orange)"><i style="background:#f4a561"><svg width="42" height="42" viewBox="0 0 42 42" fill="none" stroke="#0f1f3d" stroke-width="1.6"><circle cx="21" cy="13" r="5"/><circle cx="11" cy="17" r="4"/><circle cx="31" cy="17" r="4"/><path d="M12 33a9 9 0 0 1 18 0zM3 31a8 8 0 0 1 10-7M39 31a8 8 0 0 0-10-7"/></svg></i></div>
  <h3 class="service-name">Group Therapy</h3>
  <p class="body-copy service-text">Ut wisi enim ad minim v quis nostrud exerci taton ullamcorper spit lobortis nisl ut aliquip ex ea comghmodo consequat. Duis autem vel eum iriure dolor in hendrerit in vulputa.</p>
</div>
<div class="abs service-card" style="left:775px">
  <div class="service-icon"><i style="background:var(--teal)"><svg width="40" height="40" viewBox="0 0 40 40" fill="none" stroke="#0f1f3d" stroke-width="1.6"><circle cx="20" cy="14" r="7"/><path d="M20 7v14M14 14h12M6 20l6 12h6M34 20l-6 12h-6"/></svg></i></div>
  <h3 class="service-name">Psychiatric Services</h3>
  <p class="body-copy service-text">Ut wisi enim ad minim v quis nostrud exerci taton ullamcorper spit lobortis nisl ut aliquip ex ea comghmodo consequat. Duis autem vel eum iriure dolor in hendrerit in vulputa.</p>
</div>

<!-- Testimonials -->
<h2 class="abs heading section-title" style="top:1922px">WHAT OUR <b>CLIENTS SAY</b></h2>
<div class="abs avatar" style="left:231px;top:1917px;width:96px;height:96px" role="img" aria-label="Client portrait"></div>
<div class="abs avatar" style="left:124px;top:2065px;width:66px;height:66px" role="img" aria-label="Client portrait"></div>
<div class="abs avatar" style="left:251px;top:2186px;width:80px;height:80px" role="img" aria-label="Client portrait"></div>
<div class="abs avatar" style="left:984px;top:1940px;width:112px;height:112px" role="img" aria-label="Client portrait"></div>
<div class="abs avatar" style="left:896px;top:2123px;width:102px;height:102px" role="img" aria-label="Client portrait"></div>
<div class="abs stars">★★★★★</div>
<p class="abs quote">"Lorem ipsum dolor sit amet, consectetuer adipiscing elit, sed diam nonummy nibh euismod tincidunt ut laoreet dolore magna aliquam erat volutpat. Ut wisi enim ad minim veniam, quis nostrud exerci tation ullamcorper suscipit lobortis nisl ut aliquip ex ea commodo consequat. Duis autem vel eum iriure dolor in hendrerit in vulputate velit."</p>
<div class="abs client-name">DANA &amp; OWEN L.</div>
<div class="abs client-place">Austin, TX</div>
<div class="abs dots"><i></i><i class="on"></i><i></i></div>

<!-- Why choose -->
<div class="abs band" style="top:2358px;height:712px"></div>
<h2 class="abs heading section-title" style="top:2442px">WHY <b>CHOOSE US</b></h2>
<svg class="abs" style="left:380px;top:2490px" width="440" height="440" viewBox="0 0 440 440">
  <circle cx="220" cy="190" r="190" fill="#fff"/>
  <path d="M30 190A190 190 0 0 1 220 0" stroke="var(--teal)" stroke-width="2" fill="none"/>
  <path d="M220 0A190 190 0 0 1 410 190" stroke="var(--teal)" stroke-width="2" fill="none"/>
  <path d="M30 190A190 190 0 0 0 140 362" stroke="var(--teal)" stroke-width="2" fill="none"/>
  <path d="M410 190A190 190 0 0 1 250 378" stroke="var(--orange)" stroke-width="2" fill="none"/>
  <circle cx="110" cy="32" r="4" fill="#fff" stroke="var(--teal)"/>
  <circle cx="410" cy="190" r="4" fill="#fff" stroke="var(--orange)"/>
  <circle cx="137" cy="360" r="4" fill="#fff" stroke="var(--teal)"/>
  <circle cx="220" cy="190" r="46" fill="var(--teal)" opacity=".45"/>
</svg>
<svg class="abs" style="left:375px;top:2545px" width="120" height="120" viewBox="0 0 120 120">
  <path d="M8 60a52 52 0 0 0 52 52" stroke="var(--teal)" stroke-width="10" fill="none"/>
  <circle cx="58" cy="56" r="48" fill="#fff" stroke="#eee"/>
  <g fill="none" stroke="#0f1f3d" stroke-width="2"><rect x="42" y="38" width="28" height="36" rx="2"/><path d="M48 48h16M48 56h16M48 64h8"/><circle cx="72" cy="70" r="9"/><path d="M72 65v5l3 2"/></g>
</svg>
<svg class="abs" style="left:705px;top:2545px" width="120" height="120" viewBox="0 0 120 120">
  <path d="M112 60a52 52 0 0 1-52 52" stroke="var(--teal)" stroke-width="10" fill="none"/>
  <circle cx="62" cy="56" r="48" fill="#fff" stroke="#eee"/>
  <g fill="none" stroke="#0f1f3d" stroke-width="2"><circle cx="62" cy="46" r="10"/><path d="M44 80a18 18 0 0 1 36 0z"/><path d="M52 44a10 10 0 0 1 20 0"/></g>
</svg>
<svg class="abs" style="left:540px;top:2820px" width="120" height="120" viewBox="0 0 120 120">
  <path d="M6 60a54 54 0 0 1 108 0" stroke="var(--orange)" stroke-width="10" fill="none"/>
  <circle cx="60" cy="64" r="48" fill="#fff" stroke="#eee"/>
  <g fill="none" stroke="#0f1f3d" stroke-width="2"><circle cx="60" cy="64" r="22"/><circle cx="60" cy="64" r="15"/><circle cx="60" cy="59" r="5"/><path d="M51 72a9 9 0 0 1 18 0"/></g>
</svg>
<div class="abs feature-left"><h3 class="feature-title">Flexible Scheduling</h3><p class="feature-text">We offer evening and weekend appointments to accommodate your busy lifestyle.</p></div>
<div class="abs feature-right"><h3 class="feature-title">Experienced Therapists</h3><p class="feature-text">Our team consists of licensed professionals with years of experience in various mental health specialties.</p></div>
<div class="abs feature-bottom"><h3 class="feature-title">Personalized Approach</h3><p class="feature-text">We develop individualized treatment plans tailored to your unique needs and circumstances.</p></div>

<!-- Contact -->
<h2 class="abs heading section-title" style="top:3152px">GET IN <b>TOUCH</b></h2>
<p class="abs body-copy contact-intro">Lorem ipsum dolor sit amet, consectetuer adipiscing elit sed diam<br>nonummy nibh euismod tincidunt.</p>
<div class="abs field" style="left:303px;top:3268px;width:289px"><span class="field-icon"><svg width="11" height="11" viewBox="0 0 12 12"><circle cx="6" cy="3.5" r="3" fill="#f4a561"/><path d="M0 12a6 6 0 0 1 12 0z" fill="#f4a561"/></svg></span>First Name*</div>
<div class="abs field" style="left:608px;top:3268px;width:289px"><span class="field-icon"><svg width="11" height="11" viewBox="0 0 12 12"><circle cx="6" cy="3.5" r="3" fill="#f4a561"/><path d="M0 12a6 6 0 0 1 12 0z" fill="#f4a561"/></svg></span>Last Name*</div>
<div class="abs field" style="left:303px;top:3324px;width:289px"><span class="field-icon"><svg width="11" height="11" viewBox="0 0 24 24"><path fill="#f4a561" d="M6.6 10.8a15 15 0 0 0 6.6 6.6l2.2-2.2c.3-.3.7-.4 1-.2 1.1.4 2.3.6 3.6.6.6 0 1 .4 1 1V20c0 .6-.4 1-1 1A17 17 0 0 1 3 4c0-.6.4-1 1-1h3.5c.6 0 1 .4 1 1 0 1.3.2 2.5.6 3.6.1.3 0 .7-.2 1z"/></svg></span>Your Phone*</div>
<div class="abs field" style="left:608px;top:3324px;width:289px"><span class="field-icon"><svg width="12" height="9" viewBox="0 0 26 20"><rect width="26" height="20" rx="2" fill="#f4a561"/><path d="M1 2l12 9 12-9" stroke="#fff" stroke-width="2" fill="none"/></svg></span>Your Email*</div>
<div class="abs field field-area" style="left:303px;top:3380px;width:594px"><span class="field-icon"><svg width="13" height="11" viewBox="0 0 26 22"><path d="M2 2h16v10H8l-5 4z" fill="#f4a561"/><path d="M20 6h4v10l-4-3h-8v-1h8z" fill="#f4a561"/></svg></span><span>Your Message</span></div>
<div class="btn btn-submit">Submit Now</div>

<!-- CTA -->
<div class="abs cta-photo" role="img" aria-label="Photo of a person meditating on a wooden pier facing a calm mountain lake"></div>
<h2 class="abs cta-title">READY TO START YOUR <b>JOURNEY TO WELLNESS?</b></h2>
<p class="abs cta-sub">Schedule a consultation with one of our experienced therapists today.</p>
<div class="btn btn-cta">Schedule Consultation</div>

<!-- Footer -->
<footer class="abs footer"></footer>
<div class="abs" style="left:143px;top:4043px">
  <div class="footer-head">QUICK LINKS<i></i></div>
  <ul class="footer-list"><li>• Home</li><li>• About Us</li><li>• Services</li><li>• Our Team</li><li>• Contact Us</li></ul>
</div>
<div class="abs" style="left:370px;top:4043px;width:260px">
  <div class="footer-head">CONTACT DETAILS<i></i></div>
  <div class="contact-row" style="margin-top:22px"><svg width="12" height="14" viewBox="0 0 12 16"><path d="M6 0a6 6 0 0 1 6 6c0 4-6 10-6 10S0 10 0 6a6 6 0 0 1 6-6z" fill="#fff"/><circle cx="6" cy="6" r="2" fill="#0f1f3d"/></svg><div><b>ADDRESS</b>1450 Harbor Row NW Suite 210<br>Washington, DC.</div></div>
  <div class="contact-row"><svg width="12" height="12" viewBox="0 0 24 24"><path fill="#fff" d="M6.6 10.8a15 15 0 0 0 6.6 6.6l2.2-2.2c.3-.3.7-.4 1-.2 1.1.4 2.3.6 3.6.6.6 0 1 .4 1 1V20c0 .6-.4 1-1 1A17 17 0 0 1 3 4c0-.6.4-1 1-1h3.5c.6 0 1 .4 1 1 0 1.3.2 2.5.6 3.6.1.3 0 .7-.2 1z"/></svg><div><b>PHONE</b>202 555 0148</div></div>
  <div class="contact-row"><svg width="13" height="10" viewBox="0 0 26 20"><rect width="26" height="20" rx="2" fill="#fff"/><path d="M1 2l12 9 12-9" stroke="#0f1f3d" stroke-width="2" fill="none"/></svg><div><b>EMAIL</b>info@lumenhealthdc.com</div></div>
</div>
<div class="abs" style="left:673px;top:4043px">
  <div class="footer-head">FOLLOW US<i></i></div>
  <div style="margin-top:14px">
    <div class="social-row"><i></i>Community</div>
    <div class="social-row"><i></i>Video Channel</div>
    <div class="social-row"><i></i>Photo Journal</div>
    <div class="social-row"><i></i>Updates</div>
  </div>
</div>
<div class="abs" style="left:885px;top:4065px;width:170px;height:170px;border-radius:50%;background:rgba(255,255,255,.08)"></div>
<div class="abs footer-rule"></div>
<div class="abs copyright">© 2025 Lumen Health Services. All Rights Reserved.</div>

</body>
</html>
```